Velmora Summit Journeys Facebook Page

I would like to have a very professional and unique Facebook page for my business
www.velmorasummitjourneys.com

```html
<!DOCTYPE html>
<html lang="en">
<head>
<meta charset="utf-8">
<title>Velmora Summit Journeys – Facebook Cover</title>
<link rel="stylesheet" href="https://fonts.googleapis.com/css2?family=Open+Sans:wght@300;400;700;800&display=swap">
<style>
  :root {
    --page-bg: #e4e4e4;
    --teal-deep: #1a7ca9;
    --teal-mid: #1f8a9c;
    --teal-soft: #2a938a;
    --white: #ffffff;
    --sky-top: #2d5fa8;
    --sky-mid: #8fb3d9;
    --snow: #e9eef5;
    --earth: #7a5233;
    --ring: rgba(255,255,255,0.75);
  }
  * { margin: 0; padding: 0; box-sizing: border-box; }
  html, body {
    width: 1200px; height: 1155px; overflow: hidden;
    background: var(--page-bg);
    font-family: "Open Sans", Arial, sans-serif;
  }
  .cover {
    position: absolute; left: 45px; top: 372px;
    width: 1110px; height: 411px;
    overflow: hidden;
    box-shadow: 0 18px 30px -14px rgba(0,0,0,0.35);
  }
  .cover-art { position: absolute; inset: 0; }
  .headline {
    position: absolute; left: 57px; top: 46px;
    color: var(--white); text-transform: uppercase;
    line-height: 52px;
  }
  .headline span { display: block; white-space: nowrap; }
  .headline .light { font-weight: 300; font-size: 40px; letter-spacing: -0.5px; }
  .headline .heavy { font-weight: 800; font-size: 53px; letter-spacing: -0.5px; }
  .brand {
    position: absolute; right: 52px; top: 34px;
    display: flex; align-items: center; gap: 10px;
  }
  .brand-dot {
    width: 56px; height: 56px; border-radius: 50%;
    background: var(--white);
  }
  .brand-name {
    color: var(--white); font-weight: 700; font-size: 19px;
    line-height: 22px; text-transform: uppercase; letter-spacing: 0.3px;
  }
</style>
</head>
<body>
  <section class="cover">
    <svg class="cover-art" width="1110" height="411" viewBox="0 0 1110 411">
      <defs>
        <linearGradient id="panelGrad" x1="0" y1="0" x2="1" y2="1">
          <stop offset="0" stop-color="var(--teal-deep)"/>
          <stop offset="0.6" stop-color="var(--teal-mid)"/>
          <stop offset="1" stop-color="var(--teal-soft)"/>
        </linearGradient>
        <linearGradient id="vistaGrad" x1="0" y1="0" x2="0" y2="1">
          <stop offset="0" stop-color="var(--sky-top)"/>
          <stop offset="0.35" stop-color="var(--sky-mid)"/>
          <stop offset="0.6" stop-color="var(--snow)"/>
          <stop offset="1" stop-color="var(--earth)"/>
        </linearGradient>
        <linearGradient id="peakGrad" x1="0" y1="0" x2="0" y2="1">
          <stop offset="0" stop-color="#4f7fc0"/>
          <stop offset="0.55" stop-color="#dfe6ee"/>
          <stop offset="1" stop-color="#6b6658"/>
        </linearGradient>
        <linearGradient id="templeGrad" x1="0" y1="0" x2="1" y2="1">
          <stop offset="0" stop-color="#3f5a3a"/>
          <stop offset="0.5" stop-color="#6e4a32"/>
          <stop offset="1" stop-color="#2f2a24"/>
        </linearGradient>
      </defs>
      <rect class="teal-panel" width="1110" height="411" fill="url(#panelGrad)"/>
      <polygon class="mountain-vista" points="505,0 1110,0 1110,411 495,411"
               fill="url(#vistaGrad)" role="img"
               aria-label="Photo of snowy Himalayan peaks above a brown river valley"/>
      <circle cx="440" cy="98" r="103" fill="none" stroke="var(--ring)" stroke-width="1.2"/>
      <circle cx="470" cy="262" r="138" fill="none" stroke="var(--ring)" stroke-width="1.2"/>
      <circle class="photo-peak" cx="442" cy="105" r="84" fill="url(#peakGrad)"
              role="img" aria-label="Photo of trekkers on a rocky ridge below a snowy summit"/>
      <circle class="photo-temple" cx="472" cy="262" r="124" fill="url(#templeGrad)"
              role="img" aria-label="Photo of a cliffside monastery with prayer flags"/>
    </svg>

    <h1 class="headline">
      <span class="light">Visit</span>
      <span class="heavy">The Top</span>
      <span class="light">Of The</span>
      <span class="heavy">World</span>
      <span class="light">Challenge</span>
      <span class="heavy">Yourself</span>
    </h1>

    <div class="brand">
      <div class="brand-dot"></div>
      <div class="brand-name">Velmora Summit<br>Journeys</div>
    </div>
  </section>
</body>
</html>
```